Marlowby Services Website Design

We have most content but require a professional design. We have a logo already and will need it utilized along with several of the photos from the attached documentation.
First page should have our mission and Vision and the synapsis provided in the word document. Visitors will be prompted to select from one of our 3 divisions from this page.
Each division will have the same list of tabs : About, Services, Safety, Careers and Contact.
Photos on each divisions page should be representative of the divisions offerings. The word doc attached contains the requested content and we are open to edits that would complement and fill the website.
I like the Quorvane site www.quorvane.example - they are our competition so cant be modeled directly after this.
Please include prompts to request quote at each service page. align the format of the geotechnical page to the other 2 divisions.
I used chat gpt for some of the content so will need it optimized for SCO.

```html
<!DOCTYPE html>
<html lang="en">
<head>
<meta charset="utf-8">
<title>Marlowby Services</title>
<link rel="stylesheet" href="https://fonts.googleapis.com/css2?family=Michroma&family=Montserrat:wght@400;500;600;700&display=swap">
<style>
:root{
  --red:#e8272c;
  --grey:#e6e7eb;
  --white:#ffffff;
  --ink:#2a2a2a;
  --black:#000000;
  --display:"Michroma",sans-serif;
  --body:"Montserrat",sans-serif;
}
*{box-sizing:border-box;margin:0;padding:0}
html,body{width:1200px;height:2988px;overflow:hidden}
body{position:relative;font-family:var(--body);color:var(--ink);background:var(--white)}
.abs{position:absolute}
.brand{font-family:var(--display);color:var(--white);letter-spacing:2px;white-space:nowrap}

/* hero */
.hero{left:0;top:0;width:1200px;height:575px;background:linear-gradient(135deg,#e33a3e 0%,#e8272c 55%,#d9262b 100%)}
.nav{display:flex;gap:32px;font-size:16px;font-weight:600;color:var(--white)}
.accent-line{height:2px;background:var(--white)}
.accent-dot{width:12px;height:12px;border-radius:50%;background:var(--white)}
.hero-title{left:111px;top:204px;font-family:var(--display);font-size:35px;color:var(--white);white-space:nowrap}
.hero-text{left:111px;top:273px;width:430px;font-size:17px;line-height:27px;color:var(--white)}
.btn{display:flex;align-items:center;justify-content:center;border-radius:24px;font-family:var(--display);font-size:16px;height:48px;white-space:nowrap}
.btn-light{left:111px;top:397px;width:182px;background:var(--white);color:var(--red)}
.btn-red{background:var(--red);color:var(--white)}
.dots{left:111px;top:475px;display:flex;gap:12px}
.dots span{width:9px;height:9px;border-radius:50%;background:var(--white)}
.dots span:first-child{background:transparent;border:1.5px solid var(--white)}
.truck{left:612px;top:272px;width:574px;height:232px;background:linear-gradient(180deg,#f4f4f4,#c9c9c9);border-radius:6px}

/* photo frames */
.photo{border:8px solid var(--white);box-shadow:0 2px 10px rgba(0,0,0,.08)}
.photo-aerial{background:linear-gradient(160deg,#8a9a7d,#6f7f86)}
.photo-sky{background:linear-gradient(180deg,#3f7fd0,#9cc0e8 70%,#6e7a4e)}
.photo-chart{background:linear-gradient(180deg,#f5f5f5,#dcdcdc)}
.photo-field{background:linear-gradient(180deg,#7a6a4f,#9c8a6a)}

/* split sections */
.grey-panel{background:var(--grey)}
.section-title{font-family:var(--display);font-size:22px;color:var(--red);white-space:nowrap}
.section-text{font-size:15px;line-height:27.3px;color:var(--ink)}
.red-line{height:2px;background:var(--red)}
.red-dot{width:12px;height:12px;border-radius:50%;background:var(--red)}

/* services */
.services{left:0;top:1217px;width:1200px;height:514px;background:linear-gradient(135deg,#e7353a,#e8272c 60%,#dc2429)}
.services-title{left:0;top:1272px;width:1200px;text-align:center;font-family:var(--display);font-size:22px;color:var(--white)}
.svc-label{font-family:var(--display);font-size:17px;line-height:35px;color:var(--white);white-space:nowrap}
.svc-node{width:88px;height:88px;border-radius:50%;background:var(--white);border:4px solid #f4c5c6;display:flex;align-items:center;justify-content:center}

/* divisions */
.division{display:flex;align-items:center;height:84px;width:324px;background:var(--red)}
.division-icon{width:86px;height:86px;border-radius:50%;background:var(--white);border:2px solid var(--red);display:flex;align-items:center;justify-content:center;margin-left:-1px;flex:none}
.division-name{font-family:var(--display);font-size:14px;line-height:32px;color:var(--white);padding-left:16px;white-space:nowrap}

/* footer */
.footer{left:0;top:2635px;width:1200px;height:353px;background:var(--black)}
.social{width:36px;height:36px;border-radius:50%;border:1.5px solid var(--white)}
.copyright{left:0;top:2918px;width:1200px;text-align:center;color:var(--white);font-size:14px;font-weight:500}
</style>
</head>
<body>

<!-- HERO -->
<section class="abs hero" role="img" aria-label="Red tinted aerial photo of a boom truck at a work site"></section>
<svg class="abs" style="left:0;top:0" width="1200" height="575" aria-hidden="true"><polygon points="603,575 1200,104 1200,575" fill="#f2eeee"/></svg>
<div class="abs truck" role="img" aria-label="White boom lift truck with extended aerial platform"></div>
<div class="abs brand" style="left:111px;top:46px;font-size:36px">MARLOWBY</div>
<nav class="abs nav" style="left:517px;top:58px"><span>HOME</span><span>ABOUT</span><span>SERVICES</span><span>SAFETY</span><span>CAREERS</span><span>CONTACT</span></nav>
<div class="abs accent-line" style="left:0;top:146px;width:166px"></div>
<div class="abs accent-dot" style="left:162px;top:141px"></div>
<h1 class="abs hero-title">WELCOME TO MARLOWBY</h1>
<p class="abs hero-text">Marlowby is a full-service wind energy service provider specializing in blade access and repair, service and maintenance, and trouble shooting</p>
<div class="abs btn btn-light">GET STARTED</div>
<div class="abs dots"><span></span><span></span><span></span><span></span></div>

<!-- MISSION -->
<div class="abs grey-panel" style="left:0;top:575px;width:600px;height:642px"></div>
<div class="abs red-line" style="left:1032px;top:635px;width:168px"></div>
<div class="abs red-dot" style="left:1026px;top:629px"></div>
<div class="abs photo photo-aerial" style="left:301px;top:692px;width:338px;height:232px" role="img" aria-label="Aerial view of a town with a lift truck raising a sign"></div>
<div class="abs photo photo-chart" style="left:114px;top:794px;width:301px;height:210px" role="img" aria-label="Boom lift working range chart"></div>
<div class="abs photo photo-sky" style="left:301px;top:884px;width:285px;height:217px" role="img" aria-label="Lift truck working beside a water tower"></div>
<h2 class="abs section-title" style="left:703px;top:696px">OUR MISSION</h2>
<p class="abs section-text" style="left:703px;top:742px;width:405px">At Marlowby, our mission is to deliver unparalleled aerial access, geotechnical drilling, and service and maintenance solutions, consistently exceeding our clients' expectations. We strive to achieve this by investing in cutting-edge technology, fostering a culture of safety and continuous improvement, and prioritizing environmental sustainability. Through collaboration, integrity, and dedication, we aim to contribute to the success of our clients while maintaining the highest standards of quality and professionalism.</p>
<div class="abs btn btn-red" style="left:703px;top:1091px;width:181px">LEARN MORE</div>

<!-- SERVICES -->
<section class="abs services" role="img" aria-label="Red tinted aerial photo of a street with a lift truck"></section>
<h2 class="abs services-title">OUR SERVICES</h2>
<svg class="abs" style="left:0;top:1217px" width="1200" height="514" aria-hidden="true" stroke="#fff" stroke-width="2" fill="none">
  <line x1="513" y1="203" x2="544" y2="192"/>
  <line x1="656" y1="192" x2="687" y2="203"/>
  <line x1="430" y1="290" x2="417" y2="316"/>
  <line x1="770" y1="290" x2="783" y2="316"/>
  <line x1="408" y1="429" x2="412" y2="452"/>
  <line x1="792" y1="429" x2="788" y2="452"/>
  <circle cx="413" cy="456" r="3"/>
  <circle cx="787" cy="456" r="3"/>
</svg>
<div class="abs svc-label" style="left:0;top:1332px;width:1206px;text-align:center">CONSTRUCTION</div>
<div class="abs svc-label" style="right:794px;top:1404px;text-align:right">RELIABLE AERIAL ACCESS &amp;<br>MAINTENANCE SERVICES TO<br>OIL&amp;GAS</div>
<div class="abs svc-label" style="left:800px;top:1457px">UTILITY</div>
<div class="abs svc-label" style="right:863px;top:1584px;text-align:right">DELIVERING SAFE</div>
<div class="abs svc-label" style="left:865px;top:1569px">RENEWABLE ENERGY<br>INDUSTRIES</div>
<div class="abs brand" style="left:0;top:1565px;width:1200px;text-align:center;font-size:23px;letter-spacing:1px">MARLOWBY</div>

<div class="abs svc-node" style="left:558px;top:1375px">
  <svg width="46" height="46" viewBox="0 0 46 46" fill="none" stroke="#222" stroke-width="2"><rect x="6" y="10" width="30" height="28"/><line x1="12" y1="32" x2="34" y2="8"/><path d="M28 38l8-8v8z"/></svg>
</div>
<div class="abs svc-node" style="left:424px;top:1430px">
  <svg width="46" height="46" viewBox="0 0 46 46" fill="none" stroke="#222" stroke-width="2"><rect x="8" y="18" width="12" height="22"/><rect x="24" y="10" width="14" height="30"/><line x1="4" y1="40" x2="42" y2="40"/><line x1="28" y1="18" x2="34" y2="18"/><line x1="28" y1="26" x2="34" y2="26"/></svg>
</div>
<div class="abs svc-node" style="left:690px;top:1430px">
  <svg width="46" height="46" viewBox="0 0 46 46" fill="none" stroke="#222" stroke-width="2"><circle cx="23" cy="23" r="14"/><circle cx="23" cy="23" r="5"/><line x1="23" y1="4" x2="23" y2="9"/><line x1="23" y1="37" x2="23" y2="42"/><line x1="4" y1="23" x2="9" y2="23"/><line x1="37" y1="23" x2="42" y2="23"/></svg>
</div>
<div class="abs svc-node" style="left:358px;top:1557px">
  <svg width="46" height="46" viewBox="0 0 46 46" fill="none" stroke="#222" stroke-width="2"><rect x="6" y="24" width="18" height="16"/><path d="M28 6l10 4v8c0 6-4 10-10 12-6-2-10-6-10-12v-8z"/><path d="M23 16l4 4 6-7"/></svg>
</div>
<div class="abs svc-node" style="left:754px;top:1557px">
  <svg width="46" height="46" viewBox="0 0 46 46" fill="none" stroke="#222" stroke-width="2"><circle cx="23" cy="8" r="3"/><path d="M8 18h30l4 14H4z"/><line x1="23" y1="18" x2="23" y2="32"/><line x1="6" y1="25" x2="40" y2="25"/><line x1="23" y1="32" x2="23" y2="40"/><line x1="15" y1="40" x2="31" y2="40"/></svg>
</div>

<!-- VISION -->
<div class="abs grey-panel" style="left:600px;top:1731px;width:600px;height:591px"></div>
<div class="abs red-line" style="left:0;top:1797px;width:166px"></div>
<div class="abs red-dot" style="left:162px;top:1792px"></div>
<h2 class="abs section-title" style="left:119px;top:1885px">OUR VISION</h2>
<p class="abs section-text" style="left:119px;top:1939px;width:380px">To be the leading provider of aerial access, geotechnical drilling, and service solutions, setting the standard for excellence in safety, efficiency, and environmental stewardship.</p>
<div class="abs btn btn-red" style="left:119px;top:2089px;width:182px">LEARN MORE</div>
<div class="abs photo photo-aerial" style="left:560px;top:1821px;width:337px;height:231px" role="img" aria-label="Aerial view of a residential street"></div>
<div class="abs photo photo-sky" style="left:782px;top:1923px;width:304px;height:210px" role="img" aria-label="Water tower with crew on site"></div>
<div class="abs photo photo-field" style="left:613px;top:2016px;width:284px;height:215px" role="img" aria-label="Overhead view of a boom truck in a field"></div>

<!-- SELECT DIVISION -->
<h2 class="abs section-title" style="left:0;top:2392px;width:1200px;text-align:center">SELECT DIVISION</h2>
<div class="abs division" style="left:97px;top:2466px">
  <div class="division-icon"><svg width="50" height="50" viewBox="0 0 50 50" fill="none" stroke="#222" stroke-width="2"><rect x="10" y="20" width="22" height="20" rx="2"/><path d="M14 20v-6a7 7 0 0 1 14 0v6"/><circle cx="34" cy="34" r="9"/><circle cx="34" cy="34" r="3"/></svg></div>
  <div class="division-name">AERIAL ACCESS</div>
</div>
<div class="abs division" style="left:438px;top:2466px">
  <div class="division-icon"><svg width="50" height="50" viewBox="0 0 50 50" fill="none" stroke="#222" stroke-width="2"><rect x="14" y="6" width="22" height="10"/><path d="M18 16h14l-3 12h-8z"/><path d="M25 28v16"/><path d="M21 34l8-2M21 39l8-2"/><line x1="8" y1="44" x2="42" y2="44"/></svg></div>
  <div class="division-name">GEOTECHNICAL<br>DRILLING</div>
</div>
<div class="abs division" style="left:779px;top:2466px">
  <div class="division-icon"><svg width="50" height="50" viewBox="0 0 50 50" fill="none" stroke="#222" stroke-width="2"><path d="M10 25a15 15 0 0 1 26-10"/><path d="M40 25a15 15 0 0 1-26 10"/><path d="M36 8v7h-7"/><path d="M14 42v-7h7"/><path d="M25 34c-6-4-6-12 0-16 6 4 6 12 0 16z"/></svg></div>
  <div class="division-name">RENEWABLE<br>ENERGY SERVICES</div>
</div>

<!-- FOOTER -->
<footer class="abs footer"></footer>
<div class="abs brand" style="left:0;top:2704px;width:1200px;text-align:center;font-size:34px">MARLOWBY</div>
<nav class="abs nav" style="left:0;top:2786px;width:1200px;justify-content:center">
  <span>HOME</span><span>ABOUT</span><span>SERVICES</span><span>SAFETY</span><span>CAREERS</span><span>CONTACT</span>
</nav>
<div class="abs social" style="left:539px;top:2845px" aria-label="Social link"></div>
<div class="abs social" style="left:582px;top:2845px" aria-label="Social link"></div>
<div class="abs social" style="left:625px;top:2845px" aria-label="Social link"></div>
<p class="abs copyright">@2024 COPYRIGHTS &nbsp;|&nbsp; MARLOWBY &nbsp;|&nbsp; ALL RIGHTS RESERVED</p>

</body>
</html>
```